Dental Practice Billboard Design

We are a newer dental practice in need of a simple but appealing billboard for our growing dental practice to attract new patients. The practice is owned by husband and wife dentists and is family friendly in a small town in Kentucky. We try to be very friendly and caring to our patients. Would prefer a blue background for the billboard and our tooth logo to be prominent. We are partial to the Patua One font used in the image below but please feel free to tweak it as you deem necessary. The shape of the uppercase D and lowercase g are why we like that font, so fonts with a similarly shaped “D” and “g” would work as well. Please include our phone number (555) 847-1390. Please see our website Harlowbrookdentistry.example for more info on the practice if needed. Thank you! Looking forward to seeing your creation.
Updates

The dimensions will be 12ft x 24ft (3.6576m x 7.3152m). Apologies for not including this in the original prompt. Thank you all for your submissions.

Industry/Entity Type

Dental

Font styles to use
Other font styles liked:
• Patua One

Colors
0054AA
0677BA
7BADD7
CADEEF
E8F1F8
0094D4
00A9DD
6FCCEA
C7EBF8
E9F6FB
00AB8E
00BBA5
67D7C9
C6EFE9
E9F9F6
59FF00
82FF00
B8FF75
E3FFCB
F4FFEA

Requirements
Must have
• Phone number, website, Logo, Practice name “Harlow Brook Dentistry”
Should not have
• A tagline or slogan

```html
<!DOCTYPE html>
<html lang="en">
<head>
<meta charset="utf-8">
<title>Harlow Brook Dentistry — Billboard</title>
<link href="https://fonts.googleapis.com/css2?family=Patua+One&family=Bitter:wght@600;700&display=swap" rel="stylesheet">
<style>
  :root{
    --navy:#0c2757;
    --green:#16b11e;
    --check:#2fb82f;
    --white:#ffffff;
    --rule:#c9d3e3;
    --ink:#333333;
    --page:#ffffff;
  }
  *{margin:0;padding:0;box-sizing:border-box}
  html,body{width:1071px;height:1200px;overflow:hidden;background:var(--page)}
  .billboard{
    position:absolute;left:33px;top:349px;width:1005px;height:501px;
    background:var(--navy);overflow:hidden;
  }
  .team-photo{
    position:absolute;left:192px;top:22px;width:170px;height:220px;
    border-radius:85px 85px 70px 70px;
    background:linear-gradient(160deg,#e9e3da 0%,#cbbfb2 45%,#f4f4f4 70%,#2a2a2a 100%);
  }
  .brand-mark{
    position:absolute;left:370px;top:96px;width:18px;height:18px;border-radius:50%;
    background:var(--green);
  }
  .brand-name{
    position:absolute;left:405px;top:36px;color:var(--white);
    font-family:"Patua One",serif;font-weight:400;line-height:1;
  }
  .brand-name .line-1{display:block;font-size:128px;letter-spacing:1px}
  .brand-name .line-2{display:block;font-size:54px;margin-top:8px;margin-left:-10px}
  .services-heading{
    position:absolute;left:0;right:0;top:258px;text-align:center;
    font-family:"Patua One",serif;font-size:34px;color:var(--green);letter-spacing:.5px;
  }
  .rule{position:absolute;top:277px;height:1px;background:var(--rule)}
  .rule.left{left:67px;width:288px}
  .rule.right{left:651px;width:290px}
  .service-list{
    position:absolute;top:312px;list-style:none;
    font-family:"Bitter",serif;font-weight:600;font-size:27px;color:var(--white);
  }
  .service-list li{height:35px;line-height:35px;display:flex;align-items:center}
  .service-list svg{width:18px;height:18px;margin-right:8px;flex:none}
  .col-1{left:55px}.col-2{left:286px}.col-3{left:538px}.col-4{left:749px}
  .contact-band{position:absolute;left:0;top:0;width:1005px;height:501px}
  .website{
    position:absolute;left:95px;top:440px;color:var(--white);
    font-family:"Bitter",serif;font-weight:700;font-size:31px;line-height:36px;
  }
  .phone{
    position:absolute;left:690px;top:444px;color:var(--ink);
    font-family:"Bitter",serif;font-weight:700;font-size:36px;line-height:40px;
  }
</style>
</head>
<body>
<main class="billboard">
  <div class="team-photo" role="img" aria-label="Photo of the husband and wife dentists in white coats"></div>
  <span class="brand-mark"></span>
  <h1 class="brand-name"><span class="line-1">Harlow</span><span class="line-2">Brook Dentistry</span></h1>

  <div class="rule left"></div>
  <h2 class="services-heading">OUR SERVICES</h2>
  <div class="rule right"></div>

  <svg width="0" height="0" style="position:absolute">
    <defs><symbol id="tick" viewBox="0 0 20 20"><path d="M2 11 L8 17 L18 3" fill="none" stroke="#2fb82f" stroke-width="2.6" stroke-linecap="round" stroke-linejoin="round"/></symbol></defs>
  </svg>
  <ul class="service-list col-1">
    <li><svg><use href="#tick"/></svg>Crowns</li>
    <li><svg><use href="#tick"/></svg>Root Canals</li>
    <li><svg><use href="#tick"/></svg>Extractions</li>
  </ul>
  <ul class="service-list col-2">
    <li><svg><use href="#tick"/></svg>Implants</li>
    <li><svg><use href="#tick"/></svg>Bridges</li>
    <li><svg><use href="#tick"/></svg>Clear Aligners</li>
  </ul>
  <ul class="service-list col-3">
    <li><svg><use href="#tick"/></svg>Veneers</li>
    <li><svg><use href="#tick"/></svg>Whitening</li>
    <li><svg><use href="#tick"/></svg>Fillings</li>
  </ul>
  <ul class="service-list col-4">
    <li><svg><use href="#tick"/></svg>Cleanings</li>
    <li><svg><use href="#tick"/></svg>Dentures</li>
    <li><svg><use href="#tick"/></svg>OverDentures</li>
  </ul>

  <svg class="contact-band" viewBox="0 0 1005 501" aria-hidden="true">
    <polygon points="0,425 570,425 590,501 0,501" fill="#16b11e"/>
    <polygon points="587,439 1005,439 1005,501 605,501" fill="#ffffff"/>
    <g transform="translate(55 458)" fill="none" stroke="#ffffff" stroke-width="3">
      <circle r="21"/>
      <path d="M-14 -10 q6 2 8 8 q-4 6 2 12 q2 6 -2 10 M6 -20 q-2 8 6 10 q6 0 8 6 M10 8 q4 4 2 12" stroke-width="4"/>
    </g>
    <g transform="translate(648 458)" fill="#16b11e">
      <path d="M-16 -14 q-6 6 0 16 q10 16 24 22 q8 2 12 -4 l-8 -9 q-4 4 -8 1 q-6 -5 -10 -12 q-2 -4 2 -7 z"/>
      <path d="M2 -14 a12 12 0 0 1 12 12" stroke="#16b11e" stroke-width="3" fill="none"/>
      <path d="M3 -22 a20 20 0 0 1 19 19" stroke="#16b11e" stroke-width="3" fill="none"/>
    </g>
  </svg>
  <p class="website">Harlowbrookdentistry.example</p>
  <p class="phone">(555) 847-1390</p>
</main>
</body>
</html>
```